Vantiqo custom business card design

Need a authentic, innovative business card design for a new mobile app business. I am uploading a few screen images from our app for you to view. I would like app design theme to match business card design. I can also send logo images.

```html
<!DOCTYPE html>
<html lang="en">
<head>
<meta charset="utf-8">
<title>Vantiqo Business Card</title>
<link href="https://fonts.googleapis.com/css2?family=Montserrat:wght@700;900&family=Open+Sans:wght@400;600&display=swap" rel="stylesheet">
<style>
  :root {
    --bg: #2e3033;
    --paper: #ffffff;
    --ink: #111111;
    --grey: #555555;
    --purple: #5f0a92;
    --purple-deep: #4a0672;
    --mark-dark: #1c1c1c;
  }
  * { box-sizing: border-box; margin: 0; padding: 0; }
  html, body { width: 1200px; height: 1000px; overflow: hidden; }
  body {
    background: var(--bg);
    font-family: "Open Sans", Arial, sans-serif;
    position: relative;
  }
  .card {
    position: absolute;
    left: 250px;
    width: 700px;
    height: 400px;
    background: var(--paper);
    overflow: hidden;
    box-shadow: 0 10px 30px rgba(0,0,0,.45);
  }
  .card--back { top: 60px; }
  .card--front { top: 540px; }

  /* Back */
  .back-brand {
    position: absolute;
    left: 0; right: 0; top: 70px;
    display: flex; flex-direction: column; align-items: center;
  }
  .back-brand__dot {
    width: 150px; height: 150px; border-radius: 50%;
    background: var(--purple);
  }
  .back-brand__name {
    margin-top: 14px;
    font-family: "Montserrat", Arial, sans-serif;
    font-weight: 900; font-size: 52px; color: var(--ink);
    line-height: 1;
  }
  .back-web {
    position: absolute; left: 0; right: 0; bottom: 38px;
    text-align: center; font-size: 17px; letter-spacing: 6px; color: var(--grey);
  }

  /* Front */
  .front-band {
    position: absolute; left: 0; right: 0; top: 190px; bottom: 0;
    background: linear-gradient(180deg, var(--purple) 0%, var(--purple-deep) 100%);
  }
  .front-brand {
    position: absolute; left: 40px; top: 26px;
    font-family: "Montserrat", Arial, sans-serif;
    font-weight: 900; font-size: 62px; color: var(--ink); line-height: 1;
  }
  .front-address {
    position: absolute; left: 42px; top: 112px;
    font-size: 17px; line-height: 22px; color: var(--grey);
  }
  .front-person {
    position: absolute; right: 60px; top: 118px; text-align: center;
  }
  .front-person__name {
    font-family: "Montserrat", Arial, sans-serif;
    font-weight: 700; font-size: 24px; color: var(--purple); line-height: 1.15;
  }
  .front-person__title {
    font-size: 17px; line-height: 1.2; color: var(--ink); letter-spacing: .5px;
  }
  .contact-list {
    position: absolute; left: 42px; top: 208px; list-style: none;
  }
  .contact-list li {
    display: flex; align-items: center; gap: 14px;
    color: var(--paper); font-size: 18px; line-height: 27px;
  }
  .contact-list svg { width: 16px; height: 16px; fill: var(--paper); flex: none; }
  .front-mark {
    position: absolute; left: 480px; top: 200px;
    width: 180px; height: 180px; border-radius: 50%;
    background: var(--mark-dark);
  }
</style>
</head>
<body>

<section class="card card--back" aria-label="Card back">
  <div class="back-brand">
    <div class="back-brand__dot"></div>
    <div class="back-brand__name">Vantiqo</div>
  </div>
  <p class="back-web">www.vantiqo.com</p>
</section>

<section class="card card--front" aria-label="Card front">
  <div class="front-band"></div>
  <h1 class="front-brand">Vantiqo</h1>
  <p class="front-address">2718 Harlow Lane<br>Brookfield, NY 11020</p>
  <div class="front-person">
    <p class="front-person__name">MARCUS HALE</p>
    <p class="front-person__title">PRESIDENT</p>
  </div>
  <ul class="contact-list">
    <li><svg viewBox="0 0 16 16"><path d="M2 6c0-2 2-3 6-3s6 1 6 3v1h-3V6H5v1H2z"/><rect x="3" y="8" width="10" height="6" rx="1"/></svg>555 0142 7781</li>
    <li><svg viewBox="0 0 16 16"><rect x="4" y="1" width="8" height="14" rx="1.5"/><rect x="5.5" y="3" width="5" height="8" fill="#5f0a92"/></svg>555 0193 4426</li>
    <li><svg viewBox="0 0 16 16"><rect x="4" y="1" width="8" height="5"/><rect x="1" y="6" width="14" height="8" rx="1"/></svg>555 0167 3912</li>
    <li><svg viewBox="0 0 16 16"><rect x="1" y="3" width="14" height="10"/><path d="M1 3l7 6 7-6" fill="none" stroke="#5f0a92" stroke-width="1.5"/></svg>marcus@vantiqo.com</li>
    <li><svg viewBox="0 0 16 16"><circle cx="8" cy="8" r="7"/><path d="M1 8h14M8 1c-3 4-3 10 0 14M8 1c3 4 3 10 0 14" fill="none" stroke="#5f0a92" stroke-width="1"/></svg>www.vantiqo.com</li>
  </ul>
  <div class="front-mark"></div>
</section>

</body>
</html>
```